Garland Custom Boats Website update

I would like an updated website to my current site (Garlandboats.com).
I have an updated logo i would like to incorporate.
24 pages , would like to integrate videos of the boats (that i can upload later)

Target Market(s)

Professional and Commercial boat owners

Industry/Entity Type

Custom Boat Manufacturing

Coding

Coded - Design and coding required

Number of Pages Required

5+ page

Font styles to use
Serif

Requirements
Must have
• Easy to read, well laid-out, and video integration
Nice to have
• Fresh up to date look

```html
<!DOCTYPE html>
<html lang="en">
<head>
<meta charset="utf-8">
<title>Garland Custom Boats</title>
<link href="https://fonts.googleapis.com/css2?family=Open+Sans:wght@400;600;700&family=Russo+One&display=swap" rel="stylesheet">
<style>
:root{
  --blue:#0a44a8;
  --blue-dark:#083a8f;
  --red:#c9262f;
  --yellow:#f5d000;
  --ink:#1d1d1d;
  --muted:#666;
  --grey-bg:#efefef;
  --white:#fff;
}
*{margin:0;padding:0;box-sizing:border-box}
html,body{width:1200px;height:3166px;overflow:hidden}
body{position:relative;background:var(--white);font-family:"Open Sans",sans-serif;color:var(--ink)}
.abs{position:absolute}
.display{font-family:"Russo One",sans-serif;text-transform:uppercase;letter-spacing:.5px}
.hl{position:relative;display:inline-block}
.hl::after{content:"";position:absolute;left:0;bottom:2px;width:38%;height:5px;background:var(--yellow);z-index:-1}
.hl-white::after{z-index:0;bottom:0}

/* header */
.brand{left:144px;top:26px;font-weight:700;font-size:22px;color:var(--blue);letter-spacing:.5px}
.contact-top{top:14px;display:flex;align-items:center;gap:14px;font-size:13px;color:#555}
.ico-circle{width:30px;height:30px;border:2px solid var(--red);border-radius:50%;display:flex;align-items:center;justify-content:center}
.navbar{left:290px;top:58px;width:910px;height:36px;background:var(--blue);border-top-left-radius:40px 36px}
.nav{display:flex;gap:0;position:absolute;left:36px;top:0;height:36px;align-items:center;font-size:14.5px;color:var(--white)}
.nav span{margin-right:34px}
.nav .active{color:var(--yellow)}

/* hero */
.hero{left:0;top:94px;width:1200px;height:592px;background:radial-gradient(circle at 75% 40%,#4a8fc4 0%,#1f5f99 35%,#0e3d6e 75%,#0a2f57 100%);border-radius:0 0 0 150px/0 0 0 130px;overflow:hidden}
.hero-title{left:144px;top:236px;color:var(--white);font-size:45px;line-height:64px}
.hero-sub{left:146px;top:376px;color:var(--white);font-size:18.5px;line-height:32px}
.btn{display:flex;align-items:center;gap:8px;background:var(--red);color:var(--white);font-weight:700;font-size:15px;text-transform:uppercase;border-radius:0 24px 24px 0}
.hero .dots{left:580px;top:527px;display:flex;gap:6px}
.dot{width:10px;height:10px;border:1.5px solid var(--white);border-radius:50%}
.dot.on{background:var(--white)}

/* about */
.about-block{left:115px;top:750px;width:280px;height:255px;background:var(--blue)}
.about-photo{left:145px;top:778px;width:440px;height:394px;background:linear-gradient(160deg,#9cc9ea 0%,#5f9fd0 45%,#e8e2d8 100%);border-bottom-right-radius:70px}
.about-title{left:667px;top:818px;font-size:29px}
.about-text{left:667px;top:876px;width:395px;font-size:13.5px;line-height:24px;color:var(--muted)}
.about-text p{margin-bottom:6px}

/* boats */
.boats{left:0;top:1248px;width:1200px;height:682px;background:var(--grey-bg)}
.sec-title{font-size:29px}
.boats-sub{left:144px;top:110px;font-size:18px;line-height:29px;color:var(--ink)}
.arrow-btn{width:36px;height:36px;border-radius:50%;display:flex;align-items:center;justify-content:center}
.card{width:443px;height:196px;background:var(--white);box-shadow:0 1px 4px rgba(0,0,0,.08);display:flex;padding:6px}
.card-img{width:212px;height:184px;flex:none}
.card-body{padding:28px 14px 0 24px}
.card-body h3{font-weight:400;font-size:16.5px;margin-bottom:12px}
.card-body p{font-size:13px;line-height:20px;color:var(--muted);margin-bottom:14px}
.more{color:var(--red);font-weight:700;font-size:14px;text-transform:uppercase}

/* testimonials */
.testi{left:0;top:1930px;width:1200px;height:386px;background:var(--red)}
.testi-title{left:0;width:1200px;top:60px;text-align:center;color:var(--white);font-size:31px}
.tcard{top:135px;width:296px;height:181px;background:var(--white);padding:26px 22px}
.stars{color:#f5c400;font-size:17px;letter-spacing:6px;margin-bottom:10px}
.tcard p{font-size:13px;line-height:24px;color:var(--muted);margin-bottom:12px}
.tcard .who{font-size:15px;color:var(--ink)}
.circ-outline{width:36px;height:36px;border-radius:50%;border:2px solid var(--white);display:flex;align-items:center;justify-content:center}

/* partners */
.partners-title{left:144px;top:2410px}
.tile{width:217px;height:71px;background:var(--white);box-shadow:0 2px 10px rgba(0,0,0,.07);display:flex;align-items:center;justify-content:center}
.badge{width:96px;height:30px;border-radius:6px}
.pdots{left:348px;top:2783px;display:flex;gap:5px}
.sq{width:9px;height:9px;border:1px solid #999}
.sq.on{background:var(--red);border-color:var(--red)}
.red-block{left:819px;top:2396px;width:264px;height:240px;background:var(--red)}
.partners-photo{left:640px;top:2417px;width:415px;height:398px;background:linear-gradient(180deg,#5ca9c9 0%,#9fd0e3 35%,#3a6f8c 60%,#b8b3ab 100%);border-bottom-left-radius:110px}

/* footer */
.footer{left:0;top:2884px;width:1200px;height:282px;background:var(--blue);border-radius:200px 200px 0 0/110px 110px 0 0;color:var(--white)}
.foot-brand{left:0;width:1200px;top:62px;text-align:center;font-weight:700;font-size:22px}
.foot-nav{left:144px;width:912px;top:136px;display:flex;justify-content:center;gap:22px;font-size:14.5px;text-transform:uppercase}
.rule{left:144px;width:912px;height:1px;background:rgba(255,255,255,.6)}
.foot-contact{left:144px;width:912px;top:190px;display:flex;justify-content:space-between;font-size:14px}
.foot-contact span{display:flex;align-items:center;gap:6px}
.vsep{width:1px;height:26px;background:rgba(255,255,255,.5);margin-top:-4px}
.copy{left:0;width:1200px;top:256px;text-align:center;font-size:13.5px}
</style>
</head>
<body>

<!-- header -->
<div class="abs brand">Garland Custom Boats</div>
<div class="abs contact-top" style="left:603px">
  <div class="ico-circle"><svg width="12" height="14" viewBox="0 0 12 14"><path d="M6 0a5 5 0 0 0-5 5c0 3.5 5 9 5 9s5-5.5 5-9a5 5 0 0 0-5-5zm0 7a2 2 0 1 1 0-4 2 2 0 0 1 0 4z" fill="#0a44a8"/></svg></div>
  <span>4120 Harbor Rd. Bayport, Louisiana 70399</span>
</div>
<div class="abs contact-top" style="left:932px">
  <div class="ico-circle"><svg width="13" height="13" viewBox="0 0 24 24"><path d="M6.6 10.8a15 15 0 0 0 6.6 6.6l2.2-2.2a1 1 0 0 1 1-.25 11 11 0 0 0 3.6.6 1 1 0 0 1 1 1V20a1 1 0 0 1-1 1A17 17 0 0 1 3 4a1 1 0 0 1 1-1h3.5a1 1 0 0 1 1 1 11 11 0 0 0 .6 3.6 1 1 0 0 1-.25 1z" fill="#0a44a8"/></svg></div>
  <span>555.210.4478</span>
</div>
<div class="abs navbar">
  <nav class="nav">
    <span class="active">Home</span><span>About Us</span><span>Boats &#8964;</span><span>Driving Directions</span><span>Optional Equipment</span><span>Links</span><span style="margin-right:0">Contact Us</span>
  </nav>
</div>

<!-- hero -->
<section class="abs hero" role="img" aria-label="Photo of a white motor yacht cruising fast across deep blue ocean water">
  <div class="abs dots"><div class="dot"></div><div class="dot on"></div><div class="dot"></div></div>
</section>
<h1 class="abs display hero-title"><span class="hl hl-white">Welcome to</span><br>Garland Boats</h1>
<p class="abs hero-sub">As With All Our Boats, Engine Manufacturer and<br>Power Rating Remains Your Choice.</p>
<div class="abs btn" style="left:146px;top:476px;width:180px;height:48px;padding-left:24px">Get Started
  <svg width="14" height="14" viewBox="0 0 14 14"><circle cx="7" cy="7" r="7" fill="#fff"/><path d="M5.5 4l3 3-3 3" stroke="#c9262f" stroke-width="2" fill="none"/></svg></div>

<!-- about -->
<div class="abs about-block"></div>
<div class="abs about-photo" role="img" aria-label="Photo of a family relaxing on the deck of a sailboat on a sunny day"></div>
<h2 class="abs display about-title"><span class="hl">About Us</span></h2>
<div class="abs about-text">
  <p>Welcome to Garland Boats. We build custom boats to meet our customers' specification. Our boats range in size from 26' to 71'. We specialize in Dive Boats, Yacht Sport Fisherman, Patrol Boats, and Research Vessels.</p>
  <p>Our projects are original and diverse. Quality and customer satisfaction are always our top priorities.</p>
</div>
<div class="abs btn" style="left:669px;top:1068px;width:145px;height:43px;padding-left:19px;font-size:14px">Read More
  <svg width="13" height="13" viewBox="0 0 14 14"><circle cx="7" cy="7" r="7" fill="#fff"/><path d="M5.5 4l3 3-3 3" stroke="#c9262f" stroke-width="2" fill="none"/></svg></div>

<!-- boats -->
<section class="abs boats">
  <h2 class="abs display sec-title" style="left:144px;top:52px"><span class="hl">Garland Boats</span></h2>
  <p class="abs boats-sub">Garland Boats Uses The Latest Technology &amp; Only The Highest<br>Quality Materials To Build Our Custom Boats.</p>
  <div class="abs arrow-btn" style="left:970px;top:120px;background:#fff;box-shadow:0 1px 4px rgba(0,0,0,.15)"><svg width="10" height="14" viewBox="0 0 10 14"><path d="M7 2L2 7l5 5" stroke="#222" stroke-width="2" fill="none"/></svg></div>
  <div class="abs arrow-btn" style="left:1018px;top:120px;background:var(--blue)"><svg width="10" height="14" viewBox="0 0 10 14"><path d="M3 2l5 5-5 5" stroke="#fff" stroke-width="2" fill="none"/></svg></div>

  <div class="abs card" style="left:144px;top:205px">
    <div class="card-img" role="img" aria-label="Photo of a white dive boat speeding on the water" style="background:linear-gradient(180deg,#a9c6da,#6f98b5 60%,#e9eef2)"></div>
    <div class="card-body"><h3>46' Dive Special</h3><p>Using the experience gained over the years, the suggestions given to us by dive</p><span class="more">More Details &#8250;</span></div>
  </div>
  <div class="abs card" style="left:612px;top:205px">
    <div class="card-img" role="img" aria-label="Photo of a sport fishing boat at anchor" style="background:linear-gradient(180deg,#8c8f95,#c9ccd0 50%,#5f6c78)"></div>
    <div class="card-body"><h3>46' Sport Fish</h3><p>Whether you are looking for the perfect Charter boat or just looking for your Dream</p><span class="more">More Details &#8250;</span></div>
  </div>
  <div class="abs card" style="left:144px;top:421px">
    <div class="card-img" role="img" aria-label="Photo of a research vessel docked near trees" style="background:linear-gradient(180deg,#7d8a6d,#cfd3cf 55%,#9a9281)"></div>
    <div class="card-body"><h3>46' Research Vessel</h3><p>Our 46' and 53' Garland Research Vessel is custom built for the marine research</p><span class="more">More Details &#8250;</span></div>
  </div>
  <div class="abs card" style="left:612px;top:421px">
    <div class="card-img" role="img" aria-label="Photo of a glass bottom boat under construction" style="background:linear-gradient(180deg,#b5b8bc,#e6e6e4 50%,#3d4248)"></div>
    <div class="card-body"><h3>36' Glass Bottom Boat</h3><p>We can configure this boat to be set up for touring, snorkel-ing, diving, fishing</p><span class="more">More Details &#8250;</span></div>
  </div>
</section>

<!-- testimonials -->
<section class="abs testi">
  <h2 class="abs display testi-title"><span class="hl hl-white" style="padding:0 2px">Testimonials</span></h2>
  <div class="abs circ-outline" style="left:96px;top:207px"><svg width="10" height="14" viewBox="0 0 10 14"><path d="M7 2L2 7l5 5" stroke="#fff" stroke-width="2" fill="none"/></svg></div>
  <div class="abs tcard" style="left:144px"><div class="stars">★★★★★</div><p>Lorem ipsum dolor sit amet, consectetur adipiscing elit, sed do eiusmod tempor incididunt ut labore et dolore.</p><div class="who">- Marla.T</div></div>
  <div class="abs tcard" style="left:452px"><div class="stars">★★★★★</div><p>Lorem ipsum dolor sit amet, consectetur adipiscing elit, sed do eiusmod tempor incididunt ut labore et dolore.</p><div class="who">- Prescott.R</div></div>
  <div class="abs tcard" style="left:759px"><div class="stars">★★★★★</div><p>Lorem ipsum dolor sit amet, consectetur adipiscing elit, sed do eiusmod tempor incididunt ut labore et dolore.</p><div class="who">- Ingrid,V</div></div>
  <div class="abs circ-outline" style="left:1068px;top:207px;background:#fff"><svg width="10" height="14" viewBox="0 0 10 14"><path d="M3 2l5 5-5 5" stroke="#c9262f" stroke-width="2" fill="none"/></svg></div>
</section>

<!-- partners -->
<h2 class="abs display sec-title partners-title"><span class="hl">Trusted Partners</span></h2>
<div class="abs tile" style="left:141px;top:2492px"><div class="badge" style="background:#2b2b2b"></div></div>
<div class="abs tile" style="left:373px;top:2492px"><div class="badge" style="background:#c9262f"></div></div>
<div class="abs tile" style="left:141px;top:2585px"><div class="badge" style="background:#1d4fa3"></div></div>
<div class="abs tile" style="left:373px;top:2585px"><div class="badge" style="background:#b3262c"></div></div>
<div class="abs tile" style="left:141px;top:2680px"><div class="badge" style="background:#d8353a"></div></div>
<div class="abs tile" style="left:373px;top:2680px"><div class="badge" style="background:#3b87c9"></div></div>
<div class="abs pdots"><div class="sq"></div><div class="sq on"></div><div class="sq"></div></div>
<div class="abs red-block"></div>
<div class="abs partners-photo" role="img" aria-label="Photo of motor yachts on trailers in a boat yard under a blue sky"></div>

<!-- footer -->
<footer class="abs footer">
  <div class="abs foot-brand">Garland Custom Boats</div>
  <div class="abs foot-nav"><span>Home</span><span>/</span><span>About Us</span><span>/</span><span>Boats</span><span>/</span><span>Driving Directions</span><span>/</span><span>Optional Equipment</span><span>/</span><span>Links</span><span>/</span><span>Contact Us</span></div>
  <div class="abs rule" style="top:172px"></div>
  <div class="abs foot-contact">
    <span><svg width="12" height="12" viewBox="0 0 24 24"><path d="M6.6 10.8a15 15 0 0 0 6.6 6.6l2.2-2.2a1 1 0 0 1 1-.25 11 11 0 0 0 3.6.6 1 1 0 0 1 1 1V20a1 1 0 0 1-1 1A17 17 0 0 1 3 4a1 1 0 0 1 1-1h3.5a1 1 0 0 1 1 1 11 11 0 0 0 .6 3.6 1 1 0 0 1-.25 1z" fill="#f5d000"/></svg>555.210.4478</span>
    <div class="vsep"></div>
    <span><svg width="14" height="11" viewBox="0 0 14 11"><rect width="14" height="11" rx="1" fill="#f5d000"/><path d="M0 1l7 5 7-5" stroke="#0a44a8" stroke-width="1.3" fill="none"/></svg>office@garlandboats.com</span>
    <div class="vsep"></div>
    <span><svg width="10" height="13" viewBox="0 0 12 14"><path d="M6 0a5 5 0 0 0-5 5c0 3.5 5 9 5 9s5-5.5 5-9a5 5 0 0 0-5-5zm0 7a2 2 0 1 1 0-4 2 2 0 0 1 0 4z" fill="#f5d000"/></svg>4120 Harbor Rd. Bayport, LA 70399 USA</span>
    <div class="vsep"></div>
    <span><svg width="13" height="13" viewBox="0 0 13 13"><rect x="0" y="4" width="13" height="9" rx="1" fill="#f5d000"/><rect x="3" y="0" width="7" height="5" fill="#f5d000"/></svg>(555) 210-4479</span>
  </div>
  <div class="abs rule" style="top:234px"></div>
  <div class="abs copy">Copyright © 2025 - Garland Boats, Inc - All Rights Reserved</div>
</footer>

</body>
</html>
```